graphic showing our process of education as a process called a pipeline

Also see my updated comments on discussion section.
Title of the graphic needs to be:
TITLE = The KESIMA Strategic Leadership Pipeline = larger, bold heading
SUB-TITLE = Developing a steady flow of servant leaders for Tanzania's future = under title; smaller font
change the text for each of the 7 steps to match the outcomes listed on the newly attached PDF (strategic pipeline 11x17)
Pipe should be straight or mostly straight.
Pipe should not be in a strong or dark color.
Any icons or symbols should be simple and professional, not like cartoon or childish.
We need a graphic design that shows our PROCESS, called a "pipeline," that is creating future leaders. We are a US-based non-profit that operates a Christian school in rural Tanzania for 600 students (pre-K through 12th grade). It starts with child sponsorship program that allows poor children and orphans to attend school, we have a primary school (like USA elementary school, pre-K thru 7th), and are building a secondary boarding school (like USA middle and high school, grades 8-12), where students will live on campus in dormitories. We offer education, scholarships, leadership development experiences, help finding and securing college scholarships, academic and career counseling, placements for internships and jobs, and networking and leadership development content and events to create the next generation of servant leaders for the country. Prominent colors should probably be the green, blue and black in the Tanzania flag; we want the design to communicate "smart" and "strategic." The stages of the pipeline need to be properly named; we need to show a "leak" in the pipeline after the primary school because we currently have to send our students AWAY to other boarding schools because we don't have one. As the attached recording says, this is bad for their progress. The attached pipeline graphic is very rough and NOT meant to be imitated. It is factually correct, but is busy and not attractive.

Target Market(s)

Major financial contributors and foundations that want to give money to the cause

Industry/Entity Type

non-profit/Christian ministry in education

Font styles to use
Sans Serif

Requirements
Must have
• A "smart" and strategic" feel; preferably visible when on a half page
Nice to have
• a smart, sophisticated, serious look and feel
Should not have
• an elementary school feel

```html
<!DOCTYPE html>
<html lang="en">
<head>
<meta charset="utf-8">
<title>The KESIMA Strategic Leadership Pipeline</title>
<link href="https://fonts.googleapis.com/css2?family=Montserrat:wght@500;600;700;800&display=swap" rel="stylesheet">
<style>
  :root {
    --green: #22b24c;
    --blue: #1ba1dc;
    --black: #111111;
    --yellow: #f2e51a;
    --grey: #8a8a8a;
    --tint-blue: #d9edf8;
    --tint-green: #dcf5df;
    --pipe-blue: #a9d9f1;
    --pipe-green: #ade3bb;
    --joint-blue: #6cc0e8;
    --joint-green: #6fcf88;
    --white: #ffffff;
  }
  * { box-sizing: border-box; margin: 0; padding: 0; }
  html, body { width: 1200px; height: 824px; overflow: hidden; background: var(--white); }
  body { font-family: "Montserrat", sans-serif; color: var(--black); }
  .canvas { position: relative; width: 1200px; height: 824px; }

  .title {
    position: absolute; left: 0; width: 1200px; top: 122px;
    text-align: center; font-size: 40px; font-weight: 800;
    color: var(--black); line-height: 1.1; letter-spacing: .3px;
  }
  .title .accent-green { color: var(--green); }
  .title .accent-blue { color: var(--blue); }
  .subtitle {
    position: absolute; left: 0; width: 1200px; top: 180px;
    text-align: center; font-size: 21px; font-weight: 500;
    color: var(--grey); line-height: 1.2;
  }

  .pipeline-art { position: absolute; left: 0; top: 0; }

  .figure { position: absolute; border-radius: 8px; }
  .figure--students { left: 119px; top: 218px; width: 98px; height: 50px;
    background: linear-gradient(90deg, var(--pipe-blue) 0 50%, var(--pipe-green) 50% 100%); }
  .figure--leaders { left: 978px; top: 218px; width: 124px; height: 48px;
    background: linear-gradient(90deg, var(--pipe-green) 0 35%, var(--pipe-blue) 35% 65%, var(--pipe-green) 65% 100%); }

  .stage {
    position: absolute; border: 2px dotted var(--blue); border-radius: 9px;
    background: var(--white); text-align: center; overflow: hidden;
  }
  .stage--green { border-color: var(--green); }
  .stage__head {
    background: var(--tint-blue); padding: 6px 6px 5px;
    font-size: 12.5px; font-weight: 700; line-height: 1.15; text-transform: uppercase;
  }
  .stage--green .stage__head { background: var(--tint-green); }
  .stage__head .hl-blue { color: var(--blue); }
  .stage__head .hl-green { color: var(--green); }
  .stage__body { padding: 7px 8px; font-size: 10.5px; font-weight: 500; line-height: 1.25; }

  .stage--sponsor { left: 95px; top: 275px; width: 133px; height: 89px; }
  .stage--primary { left: 139px; top: 581px; width: 203px; height: 106px; }
  .stage--secondary { left: 320px; top: 331px; width: 187px; height: 86px; }
  .stage--service { left: 482px; top: 581px; width: 203px; height: 106px; }
  .stage--higher { left: 663px; top: 326px; width: 184px; height: 108px; }
  .stage--employment { left: 831px; top: 580px; width: 195px; height: 107px; }
  .stage--employment .stage__body { padding-top: 14px; }
  .stage--hub { left: 950px; top: 273px; width: 180px; height: 91px; background: var(--black); }
  .stage--hub .stage__head { background: var(--green); color: var(--white); font-size: 13.5px; padding: 8px 4px 6px; }
  .stage--hub .stage__head .hl-yellow { color: var(--yellow); }
  .stage--hub .stage__body { color: var(--white); font-size: 11.5px; padding: 5px 4px; }

  .leak-label {
    position: absolute; left: 348px; top: 587px; width: 80px;
    text-align: center; font-size: 12.5px; font-weight: 600; color: var(--grey);
    line-height: 1.15; text-transform: uppercase;
  }
</style>
</head>
<body>
<main class="canvas">
  <h1 class="title">The <span class="accent-green">KESIMA</span> Strategic <span class="accent-blue">Leadership Pipeline</span></h1>
  <p class="subtitle">Developing a steady flow of servant leaders for Tanzania's future</p>

  <div class="figure figure--students" role="img" aria-label="Two student figures"></div>
  <div class="figure figure--leaders" role="img" aria-label="Group of leader figures with a map of Tanzania"></div>

  <svg class="pipeline-art" width="1200" height="824" viewBox="0 0 1200 824" aria-hidden="true">
    <g stroke-dasharray="2 5" stroke-linecap="round" stroke-width="3" fill="none">
      <line x1="161" y1="368" x2="161" y2="478" stroke="var(--blue)"/>
      <line x1="242" y1="527" x2="242" y2="580" stroke="var(--blue)"/>
      <line x1="412" y1="420" x2="412" y2="478" stroke="var(--green)"/>
      <line x1="585" y1="527" x2="585" y2="580" stroke="var(--blue)"/>
      <line x1="757" y1="438" x2="757" y2="478" stroke="var(--green)"/>
      <line x1="928" y1="527" x2="928" y2="580" stroke="var(--blue)"/>
      <line x1="1040" y1="368" x2="1040" y2="478" stroke="var(--green)"/>
    </g>

    <!-- straight pipe -->
    <rect x="132" y="482" width="110" height="47" fill="var(--pipe-blue)"/>
    <rect x="242" y="482" width="170" height="47" fill="var(--pipe-green)"/>
    <rect x="412" y="482" width="173" height="47" fill="var(--pipe-blue)"/>
    <rect x="585" y="482" width="172" height="47" fill="var(--pipe-green)"/>
    <rect x="757" y="482" width="171" height="47" fill="var(--pipe-blue)"/>
    <rect x="928" y="482" width="140" height="47" fill="var(--pipe-green)"/>
    <line x1="140" y1="490" x2="1060" y2="490" stroke="var(--white)" stroke-width="3" opacity=".85"/>

    <!-- end flanges -->
    <rect x="122" y="474" width="14" height="63" rx="2" fill="var(--joint-blue)"/>
    <rect x="1064" y="474" width="14" height="63" rx="2" fill="var(--joint-green)"/>

    <!-- joints -->
    <g fill="var(--joint-green)">
      <rect x="238" y="476" width="8" height="59" rx="2"/>
      <rect x="581" y="476" width="8" height="59" rx="2"/>
      <rect x="924" y="476" width="8" height="59" rx="2"/>
    </g>
    <g fill="var(--joint-blue)">
      <rect x="408" y="476" width="8" height="59" rx="2"/>
      <rect x="753" y="476" width="8" height="59" rx="2"/>
    </g>

    <!-- leak after primary -->
    <path d="M377 500 L372 518 L380 516 L374 532 L388 511 L380 513 L385 500 Z" fill="var(--white)" stroke="var(--blue)" stroke-width="1.2"/>
    <path d="M375 538 C372 548 366 554 366 561 A9 9 0 0 0 384 561 C384 554 378 548 375 538 Z" fill="var(--blue)" opacity=".7"/>
    <path d="M390 550 C387 560 381 566 381 573 A9 9 0 0 0 399 573 C399 566 393 560 390 550 Z" fill="var(--blue)"/>

    <g font-family="Montserrat, sans-serif" font-weight="800" font-size="16" fill="var(--yellow)" text-anchor="middle">
      <circle cx="161" cy="506" r="14" fill="var(--black)"/><text x="161" y="512">1</text>
      <circle cx="242" cy="506" r="14" fill="var(--black)"/><text x="242" y="512">2</text>
      <circle cx="412" cy="506" r="14" fill="var(--black)"/><text x="412" y="512">3</text>
      <circle cx="585" cy="506" r="14" fill="var(--black)"/><text x="585" y="512">4</text>
      <circle cx="757" cy="506" r="14" fill="var(--black)"/><text x="757" y="512">5</text>
      <circle cx="928" cy="506" r="14" fill="var(--black)"/><text x="928" y="512">6</text>
      <circle cx="1040" cy="506" r="14" fill="var(--black)"/><text x="1040" y="512">7</text>
    </g>
  </svg>

  <section class="stage stage--sponsor">
    <div class="stage__head">KESIMA Sponsorship Project</div>
    <div class="stage__body">Identifying students who can thrive</div>
  </section>

  <section class="stage stage--primary">
    <div class="stage__head">KESIMA Leadership<br><span class="hl-blue">Primary School</span><br>(Mbeleni)</div>
    <div class="stage__body">Brighter students in Nalowe District Utilizing KESIMA Empowerment Blueprint</div>
  </section>

  <div class="leak-label">Boarding School (Outside)</div>

  <section class="stage stage--secondary stage--green">
    <div class="stage__head">KESIMA Leadership<br><span class="hl-green">Secondary School</span><br>(Mbeleni)</div>
    <div class="stage__body">Brighter students in Tanzania</div>
  </section>

  <section class="stage stage--service">
    <div class="stage__head">KESIMA Service<br><span class="hl-blue">Leadership<br>Experience</span></div>
    <div class="stage__body">Serving Tanzania's<br>most vulnerable populations</div>
  </section>

  <section class="stage stage--higher stage--green">
    <div class="stage__head">KESIMA<br><span class="hl-green">Higher Education</span><br>Support</div>
    <div class="stage__body">Applications, scholarships &amp; ongoing support throughout university</div>
  </section>

  <section class="stage stage--employment">
    <div class="stage__head">KESIMA<br><span class="hl-blue">Employment Center</span></div>
    <div class="stage__body">Start-up incubator &amp; internship placements for KESIMA-trained graduates, career counseling</div>
  </section>

  <section class="stage stage--hub">
    <div class="stage__head">KESIMA<br><span class="hl-yellow">Leadership Hub</span></div>
    <div class="stage__body">Local &amp; national leaders training &amp; positioning</div>
  </section>
</main>
</body>
</html>
```